Holistic Psychology clinic flyer-

We need a 3 fold flyer that is both professional and zen looking with holistic elements- bilingual on both sides.
I am looking for a design that conveys the sense of confidence, yet relaxing to the eye and makes people want to pick it up and read it!
We are all about balance (yin, yang) and bringing equilibrium to a person in their quest to get better.

Target Market(s)

families adults, teens children experiencing mental health issues

Industry/Entity Type

Psychologist

Font styles to use
Serif

Colors
fbf289
cee9f5
0455a3

Requirements
Must have
• my logo (spiral) ; French one side; English on the other. Text is provided; Some color but clean, zen elements
• Easy to read text
Nice to have
• nature elements, bamboo? trees etc. sunrise or sunset?
• The sunset back ground provided in the picture is not necessary
• families?
Should not have
• too many distracting elements; not too many colors. colors must be subtle and must flow together

```html
<!DOCTYPE html>
<html lang="en">
<head>
<meta charset="utf-8">
<title>Clinique Sérénia – Trifold Flyer</title>
<link rel="stylesheet" href="https://fonts.googleapis.com/css2?family=Lora:ital,wght@0,400;0,700;1,700&family=Noto+Serif:ital,wght@0,700;1,700&family=Tinos&display=swap">
<style>
  :root {
    --page-bg: #eceef1;
    --sky-top: #3b7fc1;
    --sky-mid: #9cc2de;
    --glow: #f4dca3;
    --glow-warm: #f3cf9c;
    --water: #4a8bc5;
    --navy: #1f2a6b;
    --ink: #1b1b1b;
    --band-text: #ffffff;
  }
  * { margin: 0; padding: 0; box-sizing: border-box; }
  html, body { width: 1200px; height: 1000px; overflow: hidden; }
  body {
    background: var(--page-bg);
    font-family: "Lora", Georgia, serif;
    color: var(--ink);
  }
  .flyer {
    position: absolute;
    left: 82px; top: 90px;
    width: 1035px; height: 820px;
    display: flex;
    box-shadow: 0 6px 24px rgba(0,0,0,.18);
  }
  .panel {
    position: relative;
    width: 345px; height: 100%;
    padding: 34px 26px 0;
    overflow: hidden;
  }
  .panel + .panel { border-left: 1px solid rgba(255,255,255,.35); }
  .panel-backdrop {
    position: absolute; inset: 0; z-index: 0;
    background: linear-gradient(180deg,
      var(--sky-top) 0%, var(--sky-mid) 28%, var(--glow) 48%,
      var(--glow-warm) 60%, var(--sky-mid) 80%, var(--water) 100%);
  }
  .panel-cover .panel-backdrop {
    background: linear-gradient(180deg,
      var(--sky-top) 0%, var(--sky-mid) 30%, var(--glow) 55%,
      var(--glow-warm) 70%, var(--sky-mid) 86%, var(--water) 100%);
  }
  .panel-content { position: relative; z-index: 1; }

  .section-title {
    font-family: "Noto Serif", Georgia, serif;
    font-size: 19px; font-weight: 700;
    margin-bottom: 22px;
  }
  .service { margin-bottom: 15px; }
  .service-name { font-size: 11.5px; font-weight: 700; }
  .body-text {
    font-size: 11px; line-height: 1.42; text-align: justify;
  }
  .welcome .body-text { margin-bottom: 14px; }
  .motto {
    text-align: center; font-size: 14px; line-height: 1.3;
    margin: 18px 0 22px; letter-spacing: .02em;
  }
  .contact-call {
    text-align: center; font-size: 14px; line-height: 1.35; margin-top: 10px;
  }
  .contact-phone {
    text-align: center; font-family: "Noto Serif", Georgia, serif;
    font-weight: 700; font-size: 19px; margin-top: 36px;
  }
  .contact-email { text-align: center; font-size: 15px; margin-top: 2px; }

  .clinic-name {
    font-family: "Noto Serif", Georgia, serif;
    font-weight: 700; font-size: 44px; line-height: 1.02;
    color: var(--navy); margin-bottom: 22px;
  }
  .tagline {
    font-family: "Noto Serif", Georgia, serif;
    font-style: italic; font-weight: 700;
    font-size: 17px; line-height: 1.3; margin-bottom: 20px;
  }
  .audience { list-style: none; }
  .audience li {
    font-family: "Noto Serif", Georgia, serif;
    font-style: italic; font-weight: 700; font-size: 14px;
    margin-bottom: 5px; display: flex; align-items: center; gap: 10px;
  }
  .audience li::before {
    content: ""; width: 8px; height: 8px; border-radius: 50%; background: var(--ink);
  }
  .brand {
    position: absolute; left: 0; right: 0; top: 590px;
    text-align: center; z-index: 1;
  }
  .brand-name {
    font-family: "Lora", Georgia, serif; font-size: 40px; color: var(--navy);
  }
  .address {
    position: absolute; left: 0; right: 0; top: 680px; z-index: 1;
    text-align: center; font-style: normal;
    font-family: "Tinos", "Times New Roman", serif;
    font-size: 12.5px; line-height: 1.35;
  }
  .address .tel { font-size: 15px; }
  .web-band {
    position: absolute; left: 0; right: 0; bottom: 22px; z-index: 1;
    height: 24px; background: var(--navy); color: var(--band-text);
    display: flex; align-items: center; justify-content: center;
    font-family: "Tinos", "Times New Roman", serif; font-size: 14px; letter-spacing: .32em;
  }
</style>
</head>
<body>
<main class="flyer">

  <section class="panel panel-services">
    <div class="panel-backdrop" role="img" aria-label="Soft sunset sky over calm water"></div>
    <div class="panel-content">
      <h2 class="section-title">Our Professional Services</h2>
      <div class="service">
        <h3 class="service-name">Clinical Psychology</h3>
        <p class="body-text">Psychologists are people specialists. Learn how to better understand both yourself and those in your life. Release some of the emotional and relational distress that drains you. It's time for change!</p>
      </div>
      <div class="service">
        <h3 class="service-name">Integrative Psychotherapy</h3>
        <p class="body-text">We distill the very best approaches in psychology to help you free your mind, balance your body and heal your spirit. We specialize in helping you understand and harmonize the mind-body connection.</p>
      </div>
      <div class="service">
        <h3 class="service-name">Life Coaching</h3>
        <p class="body-text">Life's challenges are opportunities for your growth. Our life coaches are skilled, caring and passionate about supporting you. Come in, it's time to discover your potential!</p>
      </div>
      <div class="service">
        <h3 class="service-name">Sports Psychology</h3>
        <p class="body-text">There are many different psychological benefits of sports. Our sports psychologists can work with you to release your mental blocks, improve your performance and ensure success! Dare to aim high!</p>
      </div>
      <div class="service">
        <h3 class="service-name">Psycho-Educational Assessments</h3>
        <p class="body-text">With the aid of psychometric tests, we can help you to figure out how your mind or that of your child works. We will highlight strengths and give recommendations to remedy any weaknesses. A detailed report and an academic intervention plan is customized for individuals aged 4-64!</p>
      </div>
      <div class="service">
        <h3 class="service-name">Mindfulness Meditation Classes</h3>
        <p class="body-text">Meditation is much more than a relaxation technique. Mindfulness will bring you a heightened awareness and improved quality of life. These classes are offered weekly and will be useful to you to learn how to meditate and integrate it into your daily life. Find your inner peace!</p>
      </div>
    </div>
  </section>

  <section class="panel panel-welcome welcome">
    <div class="panel-backdrop" role="img" aria-label="Soft sunset sky over calm water"></div>
    <div class="panel-content">
      <h2 class="section-title">Welcome to Sérénia !</h2>
      <p class="body-text">We present you with a whole new way of achieving wellness in your life. We offer a variety of clinical and educational services in a professional and peaceful environment. We use an integrative approach.</p>
      <p class="body-text">We are delighted to present you with several effective and scientific approaches that can help you. We offer a variety of clinical and educational services in a professional and peaceful environment. We are committed to supporting you in reaching your potential and feeling better by adhering to an integrative mind-body approach.</p>
      <p class="body-text">We are passionate about supporting you in reaching your potential and feeling well. It's time to start thinking of you...</p>
      <p class="motto">CALM YOUR MIND,<br>RELAX YOUR BODY,<br>NOURISH YOUR SPIRIT.</p>
      <p class="body-text">Julien Marchetti, BSc, MA. is the founder and director of Sérénia. As a clinical psychologist, author and motivational speaker with 26 years of experience, Julien is a pioneer in holistic psychology, an integrative approach that promotes healing and wellness. He and his staff are skilled in using cutting edge mind-body-spirit tools to help you with a variety of health, relational, educational and parenting issues. We look forward to supporting you and your family</p>
      <p class="contact-call">Contact us today for a<br>free phone consultation</p>
      <p class="contact-phone">514-555-0174</p>
      <p class="contact-email">info@serenia-clinic.com</p>
    </div>
  </section>

  <section class="panel panel-cover">
    <div class="panel-backdrop" role="img" aria-label="Illustration area: sunset over the sea with birds in flight"></div>
    <div class="panel-content">
      <h1 class="clinic-name">Clinique<br>Sérénia</h1>
      <p class="tagline">Psychologists<br>and Educational<br>Professionals<br>with an Integrative<br>Approach</p>
      <ul class="audience">
        <li>Children</li>
        <li>Teens</li>
        <li>Adults</li>
        <li>Couples</li>
      </ul>
    </div>
    <div class="brand">
      <span class="brand-name">Sérénia</span>
    </div>
    <address class="address">
      4580 Riverside Blvd , Beaconsfield,<br>
      Québec H9W 2K3<br>
      <span class="tel">Tel: (514) 555-0174</span><br>
      info@serenia-clinic.com<br>
      www.facebook.com/SereniaClinic
    </address>
    <div class="web-band">www.serenia-clinic.com</div>
  </section>

</main>
</body>
</html>
```